Wordpress Design Project for Bankruptcy Law Office in San Francisco

our current website: www.dorvanelilaw-example.com

we would like to re-design it for wordpress to make it faster and a bit more modern.

content should be similar to what we have there right now but also we do family law

please include logo for law office:

Law Office of Marta K. Dolvenidze

Thank you.
Updates

please see attached word document with logos that we like as an example.

we do tend to like color red.  darker red.

Please submit your design variations and logo as soon as possible.   We would like to go over them and make our decision

Reason: Please create couple of more variations of logo for your design, so we can make our decision what we like the most. Please see word doc for samples: Text: Law Office Of Marta K. Dolvenidze

Reason: final touches

Target Market(s)

bankruptcy and family law clients

Industry/Entity Type

Family Law

Requirements
Must have
• see examples of law sites
http://promo.lexorbin-example.com/testimonials

- new logo: Law Office of Marta K. Dolvenidze
- client intake form
- blog
- contact us form

Nice to have
• - map
- red color
- on the front page a nice photo of SF or a happy family

```html
<!DOCTYPE html>
<html lang="en">
<head>
<meta charset="utf-8">
<title>Law Office of Marta K. Dolvenidze</title>
<link href="https://fonts.googleapis.com/css2?family=Source+Sans+3:wght@400;600&display=swap" rel="stylesheet">
<style>
:root{
  --red:#c0140c;
  --red-dark:#8e0c07;
  --ink:#3a3a3a;
  --ink-soft:#555;
  --page:#f4f4f4;
  --panel:#ffffff;
  --rule:#cfcfcf;
}
*{box-sizing:border-box;margin:0;padding:0}
html,body{width:1188px;height:1200px;overflow:hidden}
body{background:var(--page);font-family:"Source Sans 3",sans-serif;color:var(--ink);position:relative}
.top-strip{position:absolute;left:0;top:0;width:1188px;height:8px;background:var(--red)}
.brand{position:absolute;left:77px;top:8px;width:452px;height:97px;background:var(--red);display:flex;align-items:center;padding-left:22px;gap:16px}
.brand-dot{width:46px;height:46px;border-radius:50%;background:#fff;flex:none}
.brand-name{color:#fff;font-size:25px;font-weight:400;letter-spacing:1.5px;line-height:30px;text-transform:uppercase}
.search{position:absolute;left:920px;top:54px;width:195px;height:27px;background:#fff;border:1px solid #d0d0d0;box-shadow:0 1px 2px rgba(0,0,0,.15);font-size:11px;font-style:italic;color:#aaa;padding:6px 14px}
.search svg{position:absolute;right:6px;top:7px}
.nav-band{position:absolute;left:0;top:136px;width:1188px;height:30px;background:var(--red)}
.nav{position:absolute;left:73px;top:124px;width:1044px;height:52px;display:flex;background:linear-gradient(#c8160d,#a10f09);border-radius:3px 3px 0 0;box-shadow:0 2px 3px rgba(0,0,0,.25)}
.nav a{display:flex;align-items:center;justify-content:center;color:#fff;text-decoration:none;font-size:14.5px;border-right:1px solid rgba(0,0,0,.22)}
.nav a:last-child{border-right:none}
.nav a.is-active{background:linear-gradient(#d4291f,#b3130b)}
.hero{position:absolute;left:72px;top:186px;width:1046px;height:323px;border:3px solid #d5d5d5;background:linear-gradient(90deg,#a9a09e 0%,#c7bebd 35%,#948a87 70%,#5e5452 100%)}
.hero-photo{position:absolute;inset:0;background:linear-gradient(180deg,rgba(255,255,255,0) 70%,rgba(120,80,60,.45) 100%)}
.hero-title{position:absolute;left:77px;top:82px;font-size:32px;font-weight:400;color:#333;letter-spacing:-.5px}
.hero-dots{position:absolute;left:28px;top:285px;display:flex;gap:12px}
.hero-dots span{width:11px;height:11px;border-radius:50%;background:#444}
.hero-dots span.is-current{background:var(--red-dark)}
.panel{position:absolute;left:72px;top:523px;width:1046px;height:593px;background:var(--panel)}
.panel h2{position:absolute;font-size:20px;font-weight:400;color:var(--red);z-index:1}
.welcome-title{left:21px;top:30px}
.welcome-text{position:absolute;z-index:1;left:21px;top:67px;width:690px;font-size:13.5px;line-height:24px;color:var(--ink-soft);text-align:justify}
.ticks{position:absolute;z-index:1;top:204px;list-style:none;font-size:13.5px;color:#333}
.ticks li{height:28px;display:flex;align-items:center;gap:12px}
.ticks svg{flex:none}
.ticks-a{left:45px}.ticks-b{left:370px}
.person-photo{position:absolute;left:716px;top:6px;width:330px;height:303px;background:linear-gradient(180deg,#f6f4f7 0%,#e6e3ec 50%,#ffffff 100%)}
.divider{position:absolute;left:21px;top:338px;width:1004px;height:1px;background:var(--rule)}
.news-title{left:21px;top:367px}
.about-title{left:562px;top:367px}
.dots{position:absolute;top:408px;height:0;border-top:2px dotted #999}
.dots-news{left:21px;width:502px}.dots-about{left:562px;width:460px}
.news-item{position:absolute;left:21px;width:502px;display:flex;gap:18px}
.news-icon{width:34px;height:34px;border-radius:50%;background:#ddd;flex:none;display:flex;align-items:center;justify-content:center;margin-top:3px}
.news-body{font-size:12.5px;line-height:19.5px;color:var(--ink-soft);text-align:justify}
.news-date{color:var(--red);font-style:italic}
.about-text{position:absolute;left:562px;top:431px;width:276px;font-size:12.5px;line-height:19.5px;color:var(--ink-soft);text-align:justify}
.view-more{position:absolute;left:562px;top:533px;font-size:12.5px;font-style:italic;color:var(--red);text-decoration:none}
.justice-photo{position:absolute;left:855px;top:433px;width:169px;height:111px;border-radius:3px;background:linear-gradient(135deg,#f1e4c9 0%,#c9a36b 55%,#8a6132 100%)}
.footer-links{position:absolute;left:72px;top:1136px;font-size:12.5px;color:#444;display:flex;gap:8px}
.footer-links span{color:#888}
.copyright{position:absolute;left:72px;top:1162px;font-size:12.5px;color:#444}
.social{position:absolute;top:1142px;width:33px;height:33px;border-radius:50%;background:#9a9a9a}
.social-a{left:1025px}.social-b{left:1072px;background:#b5b5b5}
</style>
</head>
<body>
<div class="top-strip"></div>
<header class="brand">
  <span class="brand-dot"></span>
  <span class="brand-name">Law Office of<br>Marta K. Dolvenidze</span>
</header>
<div class="search">Search
  <svg width="12" height="12" viewBox="0 0 12 12"><circle cx="5" cy="5" r="3.5" fill="none" stroke="#bbb" stroke-width="1.4"/><line x1="7.5" y1="7.5" x2="11" y2="11" stroke="#bbb" stroke-width="1.6"/></svg>
</div>
<div class="nav-band"></div>
<nav class="nav">
  <a class="is-active" style="width:108px">HOME</a>
  <a style="width:122px">ABOUT US</a>
  <a style="width:117px">LAWYERS</a>
  <a style="width:141px">LATEST NEWS</a>
  <a style="width:162px">LATEST ARTICLES</a>
  <a style="width:162px">PRACTICE AREAS</a>
  <a style="width:136px">CONTACT US</a>
  <a style="width:96px">FAQ</a>
</nav>
<section class="hero">
  <div class="hero-photo" role="img" aria-label="Photo of a wooden judge's gavel resting on its block"></div>
  <h1 class="hero-title">DUIS AUTE IRURE DOLOR</h1>
  <div class="hero-dots"><span class="is-current"></span><span></span><span></span><span></span></div>
</section>
<main class="panel">
  <div class="person-photo" role="img" aria-label="Photo of a smiling lawyer in shirt and tie leaning on a desk"></div>
  <h2 class="welcome-title">WELCOME TO OUR SITE</h2>
  <p class="welcome-text">Sed ut perspiciatis unde omnis iste natus error sit voluptatem accusantium doloremque laudantium, totam rem aperiam, eaque ipsa quae ab illo inventore veritatis et quasi architecto beatae vitae dicta sunt explicabo. Nemo enim ipsam voluptatem quia voluptas sit aspernatur aut odit aut fugit, sed quia consequuntur magni dolores eos qui ratione voluptatem sequi nesciunt. Neque porro quisquam est, qui dolorem ipsum quia dolor sit amet, consectetur, adipisci velit, sed quia non numquam eius modi tempora incidunt ut labore et dolore magnam aliquam.</p>
  <ul class="ticks ticks-a">
    <li><svg width="12" height="12" viewBox="0 0 12 12"><circle cx="6" cy="6" r="6" fill="#666"/><path d="M4 6h4M6 4l2 2-2 2" fill="none" stroke="#fff" stroke-width="1.4"/></svg>Duis accumsan aliquet arcu, vitae</li>
    <li><svg width="12" height="12" viewBox="0 0 12 12"><circle cx="6" cy="6" r="6" fill="#666"/><path d="M4 6h4M6 4l2 2-2 2" fill="none" stroke="#fff" stroke-width="1.4"/></svg>Morbi non lacus scelerisque nisl rhoncus</li>
    <li><svg width="12" height="12" viewBox="0 0 12 12"><circle cx="6" cy="6" r="6" fill="#666"/><path d="M4 6h4M6 4l2 2-2 2" fill="none" stroke="#fff" stroke-width="1.4"/></svg>Pellentesque pellentesque</li>
    <li><svg width="12" height="12" viewBox="0 0 12 12"><circle cx="6" cy="6" r="6" fill="#666"/><path d="M4 6h4M6 4l2 2-2 2" fill="none" stroke="#fff" stroke-width="1.4"/></svg>Cras venenatis massa ut orci pretium sit</li>
  </ul>
  <ul class="ticks ticks-b">
    <li><svg width="12" height="12" viewBox="0 0 12 12"><circle cx="6" cy="6" r="6" fill="#666"/><path d="M4 6h4M6 4l2 2-2 2" fill="none" stroke="#fff" stroke-width="1.4"/></svg>Duis accumsan aliquet arcu, vitae</li>
    <li><svg width="12" height="12" viewBox="0 0 12 12"><circle cx="6" cy="6" r="6" fill="#666"/><path d="M4 6h4M6 4l2 2-2 2" fill="none" stroke="#fff" stroke-width="1.4"/></svg>Morbi non lacus scelerisque nisl rhoncus</li>
    <li><svg width="12" height="12" viewBox="0 0 12 12"><circle cx="6" cy="6" r="6" fill="#666"/><path d="M4 6h4M6 4l2 2-2 2" fill="none" stroke="#fff" stroke-width="1.4"/></svg>Pellentesque pellentesque</li>
    <li><svg width="12" height="12" viewBox="0 0 12 12"><circle cx="6" cy="6" r="6" fill="#666"/><path d="M4 6h4M6 4l2 2-2 2" fill="none" stroke="#fff" stroke-width="1.4"/></svg>Cras venenatis massa ut orci pretium sit</li>
  </ul>
  <div class="divider"></div>
  <h2 class="news-title">LATEST NEWS</h2>
  <div class="dots dots-news"></div>
  <h2 class="about-title">ABOUT US</h2>
  <div class="dots dots-about"></div>
  <article class="news-item" style="top:431px">
    <span class="news-icon"><svg width="16" height="16" viewBox="0 0 16 16"><rect x="1" y="1" width="11" height="11" fill="none" stroke="#fff" stroke-width="2"/><rect x="5" y="5" width="10" height="10" fill="#fff"/></svg></span>
    <p class="news-body">Sed ut perspiciatis unde omnis iste natus error sit voluptatem accusantium dolor emque laudantium, totam rem aperiam, eaque ipsa quae ab illo inventore veritatis<br><span class="news-date">August 29th, 2012</span></p>
  </article>
  <article class="news-item" style="top:508px">
    <span class="news-icon"><svg width="16" height="16" viewBox="0 0 16 16"><rect x="1" y="1" width="11" height="11" fill="none" stroke="#fff" stroke-width="2"/><rect x="5" y="5" width="10" height="10" fill="#fff"/></svg></span>
    <p class="news-body">Sed ut perspiciatis unde omnis iste natus error sit voluptatem accusantium dolor emque laudantium, totam rem aperiam, eaque ipsa quae ab illo inventore veritatis<br><span class="news-date">August 29th, 2012</span></p>
  </article>
  <p class="about-text">Sed ut perspiciatis unde omnis iste natus error sit voluptatem accusantium dolor emque laudantium, totam rem aperiam, eaque ipsa quae ab illo inventore veritatis et quasi architecto beatae vitae quas molestias excepturi sint occaecati cupiditate</p>
  <a class="view-more">View more</a>
  <div class="justice-photo" role="img" aria-label="Photo of a Lady Justice statue holding scales"></div>
</main>
<footer>
  <div class="footer-links">Home <span>|</span> About us <span>|</span> Lawyers <span>|</span> Latest News <span>|</span> Latest Articles <span>|</span> Practice Areas <span>|</span> Contact us <span>|</span> FAQ</div>
  <p class="copyright">Copyright © 2012 www.dorvanelilaw-example.com &nbsp;&nbsp; All rights reserved.</p>
  <span class="social social-a"></span>
  <span class="social social-b"></span>
</footer>
</body>
</html>
```